IT Consulting Business needs a web design

We need a web design for an IT Consulting company called "Vorensk". We want to replace the existing web site (www.vorensk-example.com) with a new design. Our services are IT Consulting, IT Training, IT Outsourcing.
We would like to see designs that communicate "Trusted IT Advisor" with modern & bold design.

We would like to see the design of 2 pages:
1. Home page (www.vorensk-example.com)
2. The detail page (http://www.vorensk-example.com/index_files/consulting.htm)

Industry/Entity Type

Business

```html
<!DOCTYPE html>
<html lang="en">
<head>
<meta charset="utf-8">
<title>Vorensk – IT Consulting</title>
<link rel="stylesheet" href="https://fonts.googleapis.com/css2?family=PT+Sans:wght@400;700&family=Arimo:wght@700&display=swap">
<style>
:root{
  --blue:#1c63c6;
  --blue-dark:#1556b0;
  --red:#e5141b;
  --red-bright:#f01f1f;
  --grey-head:#6f6f6f;
  --grey-text:#555;
  --rule:#d8d8d8;
  --white:#fff;
}
*{margin:0;padding:0;box-sizing:border-box}
html,body{width:1154px;height:1200px;overflow:hidden;background:var(--white)}
body{position:relative;font-family:"PT Sans",sans-serif;color:var(--grey-text)}
.abs{position:absolute}

/* header */
.site-header{position:absolute;left:0;top:0;width:1154px;height:72px;border-bottom:3px solid #d4d4d4}
.brand{position:absolute;left:154px;top:14px;font-family:"PT Sans",sans-serif;font-weight:700;font-size:36px;line-height:40px;color:var(--blue)}
.main-nav{position:absolute;left:526px;top:0;height:68px;display:flex}
.main-nav a{display:block;height:68px;line-height:72px;padding:0 13px;font-size:13px;color:#666;text-decoration:none;border-right:1px solid #ececec}
.main-nav a:last-child{border-right:0}
.main-nav a.current{background:var(--blue);color:var(--white);border-top:4px solid var(--red);line-height:64px;width:60px;padding:0;text-align:center}

/* hero */
.hero{position:absolute;left:0;top:72px;width:1154px;height:392px;
  background:linear-gradient(90deg,#1d2633 0%,#2a3545 45%,#1f5fb4 70%,#1a8be0 100%)}

/* core values */
.core-values{position:absolute;left:155px;top:485px;width:844px;height:45px;background:var(--blue)}
.core-values svg{position:absolute;left:0;top:0}
.core-label{position:absolute;left:14px;top:0;line-height:45px;font-family:"Arimo",sans-serif;font-size:17px;color:var(--white)}
.core-item{position:absolute;top:0;line-height:45px;font-family:"Arimo",sans-serif;font-size:13px;color:var(--white);padding-left:18px}
.core-item::before{content:"";position:absolute;left:0;top:18px;width:6px;height:6px;border-right:2px solid var(--white);border-top:2px solid var(--white);transform:rotate(45deg)}

/* service columns */
.service{position:absolute;top:558px;width:257px;text-align:center}
.service .thumb{width:257px;height:105px;border-radius:4px}
.service h2{margin-top:16px;font-family:"Arimo",sans-serif;font-size:17px;color:var(--grey-head);line-height:20px}
.service p{margin-top:6px;font-size:12px;line-height:16px;height:70px}
.col-rule{position:absolute;top:558px;width:1px;height:264px;background:#e2e2e2}
.btn{display:inline-block;width:73px;height:28px;line-height:28px;border-radius:4px;background:linear-gradient(#f73030,var(--red));color:var(--white);font-size:12px;text-align:center;text-decoration:none}
.service .btn{margin-top:12px}
.section-shadow{position:absolute;left:40px;top:846px;width:1074px;height:8px;background:radial-gradient(ellipse at center,rgba(0,0,0,.07) 0%,rgba(0,0,0,0) 70%)}

/* lower */
.section-title{position:absolute;top:877px;font-family:"Arimo",sans-serif;font-size:16px;color:var(--grey-head);line-height:20px}
.trusted-thumb{position:absolute;left:155px;top:909px;width:257px;height:119px;border-radius:4px}
.trusted-copy{position:absolute;left:430px;top:905px;width:275px;font-size:12px;line-height:16px}
.expertise-list{position:absolute;left:742px;top:902px;width:257px;list-style:none}
.expertise-list li{position:relative;height:24.5px;line-height:23px;padding-left:16px;font-size:12px;border-bottom:1px dotted var(--rule)}
.expertise-list li:last-child{border-bottom:0}
.expertise-list li::before{content:"";position:absolute;left:0;top:9px;width:7px;height:7px;
  background:linear-gradient(90deg,var(--red) 0 3px,transparent 3px 4px,var(--red) 4px) top/7px 3px no-repeat,
             linear-gradient(90deg,var(--red) 0 3px,transparent 3px 4px,var(--red) 4px) bottom/7px 3px no-repeat}

/* footer */
.site-footer{position:absolute;left:0;top:1096px;width:1154px;height:104px;background:var(--blue);color:var(--white);font-size:12px}
.footer-nav{position:absolute;left:154px;top:21px;line-height:16px}
.footer-nav a{color:var(--white);text-decoration:none}
.footer-nav span{margin:0 6px}
.copyright{position:absolute;left:154px;top:41px;line-height:16px}
.contact{position:absolute;right:155px;top:21px;line-height:16px;display:flex;align-items:center;gap:5px}
.social{position:absolute;top:39px;width:24px;height:24px;border-radius:50%;background:#174b94}
</style>
</head>
<body>

<header class="site-header">
  <div class="brand">Vorensk</div>
  <nav class="main-nav">
    <a class="current" href="#">HOME</a>
    <a href="#">ABOUT US</a>
    <a href="#">SERVICES</a>
    <a href="#">EXPERTISES</a>
    <a href="#">CAREERS</a>
    <a href="#">CONTACT US</a>
  </nav>
</header>

<div class="hero" role="img" aria-label="Banner photo: businessman in a suit writing 'technology', 'quality' and 'success' on a blue digital world map"></div>

<div class="core-values">
  <svg width="844" height="45" viewBox="0 0 844 45">
    <polygon points="0,0 140,0 160,22.5 140,45 0,45" fill="var(--red)"/>
    <polyline points="140,0 160,22.5 140,45" fill="none" stroke="#fff" stroke-width="1.5"/>
    <polyline points="360,0 380,22.5 360,45" fill="none" stroke="#fff" stroke-width="1.5"/>
    <polyline points="586,0 606,22.5 586,45" fill="none" stroke="#fff" stroke-width="1.5"/>
  </svg>
  <div class="core-label">CORE VALUE</div>
  <div class="core-item" style="left:179px">QUALITY CONSCIOUS</div>
  <div class="core-item" style="left:416px">CUSTOMER FOCUS</div>
  <div class="core-item" style="left:659px">COMMITTED</div>
</div>

<section class="service" style="left:155px">
  <div class="thumb" role="img" aria-label="Photo: two consultants discussing at a desk with a monitor" style="background:linear-gradient(135deg,#9fb6c8,#5a6470 60%,#c9cfd6)"></div>
  <h2>CONSULTING SERVICES</h2>
  <p>Our experienced, certified professionals provides IT consulting using industry recommended practices. We are specialized in Portalis Business Productivity Platform using Portalis Collaboration..</p>
  <a class="btn" href="#">MORE</a>
</section>
<div class="col-rule" style="left:430px"></div>
<section class="service" style="left:449px">
  <div class="thumb" role="img" aria-label="Photo: trainer presenting a chart to a group at a meeting table" style="background:linear-gradient(135deg,#dfe6ec,#7a8796 55%,#e9edf1)"></div>
  <h2>TRAINING SERVICES</h2>
  <p>Our certified trainers provide in-house training for Vorensk original courses as well as customized training courses that suit your organization needs. On-Site training..</p>
  <a class="btn" href="#">MORE</a>
</section>
<div class="col-rule" style="left:723px"></div>
<section class="service" style="left:743px">
  <div class="thumb" role="img" aria-label="Photo: close-up of a keyboard key labelled Solution" style="background:linear-gradient(135deg,#4a6a9a,#a9b9d2 50%,#3d5c8c)"></div>
  <h2>SOLUTION SERVICES</h2>
  <p>Vorensk's unique solution services offer customers with the benefits of our expert consultants in designing, deploying, and implementing our solutions. Customers who want to have the solution with..</p>
  <a class="btn" href="#">MORE</a>
</section>

<div class="section-shadow"></div>

<h2 class="section-title" style="left:155px">YOUR MOST TRUSTED IT CONSULTANT</h2>
<div class="trusted-thumb" role="img" aria-label="Photo: two consultants discussing at a desk with a monitor" style="background:linear-gradient(135deg,#9fb6c8,#5a6470 60%,#c9cfd6)"></div>
<p class="trusted-copy">We are experienced, certified professionals who are experts at Information Technology (IT) consulting, solution design &amp; development, and training for medium-size businesses and large enterprises. We are committed to helping our clients quickly achieve the most appropriate solution with sustainable ROI. We are focusing on Portalis Technologies for large organizations.</p>
<a class="btn abs" style="left:632px;top:1038px" href="#">MORE</a>

<div class="col-rule" style="left:723px;top:874px;height:149px"></div>

<h2 class="section-title" style="left:742px">OUR EXPERTISES</h2>
<ul class="expertise-list">
  <li>Portalis Collaboration Technologies</li>
  <li>Business Intelligence with Datavane Server</li>
  <li>Enterprise Integration with LinkBridge Server</li>
  <li>Corvex Framework Development</li>
  <li>Q7 Flowmark</li>
</ul>
<a class="btn abs" style="left:926px;top:1038px" href="#">MORE</a>

<footer class="site-footer">
  <nav class="footer-nav">
    <a href="#">Home</a><span>|</span><a href="#">About Us</a><span>|</span><a href="#">Services</a><span>|</span><a href="#">Careers</a><span>|</span><a href="#">Expertises</a><span>|</span><a href="#">Contact Us</a>
  </nav>
  <div class="copyright">Vorensk © 2013. All Rights Reserved.</div>
  <div class="contact">
    <svg width="14" height="10" viewBox="0 0 14 10" aria-hidden="true"><path d="M1 4C1 1 4 0 7 0s6 1 6 4l-3 1-1-2H5L4 5Z M3 6h8l1 4H2Z" fill="#fff"/></svg>
    <span>1300 555 014</span>
    <span style="margin:0 4px">|</span>
    <svg width="13" height="9" viewBox="0 0 13 9" aria-hidden="true"><rect x=".5" y=".5" width="12" height="8" fill="none" stroke="#fff"/><polyline points=".5,.5 6.5,5 12.5,.5" fill="none" stroke="#fff"/></svg>
    <span>info@vorensk-example.com</span>
  </div>
  <span class="social" style="left:949px" aria-label="Social profile"></span>
  <span class="social" style="left:976px" aria-label="Social profile"></span>
</footer>

</body>
</html>
```